Heron Loan Partners Business Card

We need a business card design for our mortgage servicing company. In addition to servicing the loans of homeowners, we help homeowners with purchasing their homes and any mortgage refinancing. We would like to see designs that use the colors in the logo attached below (gold-ish yellow and navy blue), and any other design you deem fit! The design should communicate a simpler life with smart mortgages provided by Heron.

```html
<!DOCTYPE html>
<html lang="en">
<head>
<meta charset="utf-8">
<title>Heron Loan Partners Business Card</title>
<link href="https://fonts.googleapis.com/css2?family=Montserrat:wght@400;500;700;800&display=swap" rel="stylesheet">
<style>
  :root {
    --navy: #25205a;
    --gold: #e2b23a;
    --white: #ffffff;
    --ink: #1c1c24;
    --stage: #e6e6ea;
  }
  * { box-sizing: border-box; margin: 0; padding: 0; }
  html, body {
    width: 1200px; height: 880px; overflow: hidden;
    background: var(--stage);
    font-family: "Montserrat", sans-serif;
  }
  .card {
    position: absolute;
    width: 640px; height: 366px;
    overflow: hidden;
    box-shadow: 0 10px 28px rgba(0,0,0,.18);
  }
  .card--front { left: 120px; top: 50px; background: var(--navy); }
  .card--back { left: 440px; top: 464px; background: var(--white); }

  .brand {
    position: absolute;
    display: flex; align-items: center; gap: 12px;
    font-weight: 700; color: var(--gold);
    white-space: nowrap;
  }
  .brand__dot { border-radius: 50%; background: var(--gold); flex: none; }
  .card--front .brand { left: 0; right: 0; top: 0; bottom: 0; justify-content: center; font-size: 42px; }
  .card--front .brand__dot { width: 22px; height: 22px; }
  .card--back .brand { left: 40px; top: 160px; font-size: 20px; color: var(--navy); gap: 10px; }
  .card--back .brand__dot { width: 12px; height: 12px; }

  .wave { position: absolute; inset: 0; width: 640px; height: 366px; }

  .divider {
    position: absolute; left: 326px; top: 44px;
    width: 2px; height: 146px; background: var(--gold);
  }
  .contact { position: absolute; left: 352px; top: 38px; color: var(--ink); }
  .contact__name { font-size: 19px; font-weight: 800; color: var(--navy); letter-spacing: .3px; line-height: 1.2; }
  .contact__name span { color: var(--gold); }
  .contact__role { font-size: 14px; font-weight: 500; margin-top: 2px; }
  .contact__list { list-style: none; margin-top: 14px; }
  .contact__item {
    display: flex; align-items: center; gap: 10px;
    font-size: 13.5px; font-weight: 500; line-height: 16px; margin-bottom: 7px;
  }
  .contact__icon { width: 16px; height: 16px; flex: none; }
</style>
</head>
<body>
  <section class="card card--front">
    <div class="brand"><span class="brand__dot"></span>Heron Loan Partners</div>
  </section>

  <section class="card card--back">
    <svg class="wave" viewBox="0 0 640 366" aria-hidden="true">
      <path d="M0 340 C 220 320, 360 290, 440 240 C 520 200, 570 196, 640 190 L640 366 L0 366 Z" fill="var(--navy)"/>
      <path d="M0 318 C 180 300, 330 280, 420 228 C 340 268, 190 290, 0 304 Z" fill="var(--gold)"/>
    </svg>

    <div class="brand"><span class="brand__dot"></span>Heron Loan Partners</div>

    <div class="divider"></div>

    <div class="contact">
      <p class="contact__name">DANA <span>WHITFIELD</span></p>
      <p class="contact__role">Owner</p>
      <ul class="contact__list">
        <li class="contact__item">
          <svg class="contact__icon" viewBox="0 0 16 16" aria-hidden="true"><path d="M3 2h3l1 3-2 1a8 8 0 0 0 5 5l1-2 3 1v3a1 1 0 0 1-1 1A12 12 0 0 1 2 3a1 1 0 0 1 1-1z" fill="var(--gold)"/></svg>
          555.014.2290
        </li>
        <li class="contact__item">
          <svg class="contact__icon" viewBox="0 0 16 16" aria-hidden="true"><rect x="1" y="3" width="14" height="10" rx="1" fill="var(--gold)"/><path d="M1.5 4 8 9l6.5-5" stroke="var(--white)" stroke-width="1.3" fill="none"/></svg>
          info@heronloanpartners.com
        </li>
        <li class="contact__item">
          <svg class="contact__icon" viewBox="0 0 16 16" aria-hidden="true"><circle cx="8" cy="8" r="7" fill="var(--gold)"/><path d="M1 8h14M8 1c3 3 3 11 0 14M8 1c-3 3-3 11 0 14" stroke="var(--white)" stroke-width="1" fill="none"/></svg>
          www.heronloanpartners.com
        </li>
      </ul>
    </div>
  </section>
</body>
</html>
```